Business Card Design

We need a business card designed for our new company. Prefer a black card with white logo & writing.

Contact Information for Business Card

Ted Galloway, address: 7-4812 Fernhollow Road, Abbotsford, BC, V3K 8R2, Office Phone: 604-712-3390, Cell: 604-947-2164, Email: ted@resinworkshub.ca

Colors

Designer to choose only greyscale colors for use in the design.

```html
<!DOCTYPE html>
<html lang="en">
<head>
<meta charset="UTF-8">
<title>Resin Works Hub – Business Card</title>
<link href="https://fonts.googleapis.com/css2?family=Montserrat:wght@400;700;800&display=swap" rel="stylesheet">
<style>
  :root {
    --page: #2b2b2b;
    --card: #232323;
    --card-back: #1f1f1f;
    --ink: #ffffff;
    --ink-soft: #d6d6d6;
    --mark-dark: #111111;
  }
  * { margin: 0; padding: 0; box-sizing: border-box; }
  html, body { width: 1200px; height: 1200px; overflow: hidden; }
  body {
    background: var(--page);
    font-family: "Montserrat", sans-serif;
    display: flex;
    flex-direction: column;
    align-items: center;
    justify-content: center;
    gap: 50px;
  }
  .card {
    width: 880px;
    height: 503px;
    position: relative;
    overflow: hidden;
  }
  .card--front { background: var(--card); }
  .card--back {
    background: var(--card-back);
    display: flex;
    align-items: center;
    justify-content: center;
  }
  .brand {
    position: absolute;
    left: 60px;
    top: 56px;
    display: flex;
    align-items: center;
    gap: 14px;
    color: var(--ink);
    font-weight: 800;
    font-size: 34px;
    letter-spacing: 0.5px;
    text-transform: uppercase;
  }
  .brand__dot {
    width: 18px; height: 18px;
    border-radius: 50%;
    background: var(--ink);
  }
  .address {
    position: absolute;
    left: 60px;
    top: 190px;
    color: var(--ink-soft);
    font-size: 17px;
    line-height: 1.4;
  }
  .contact-list {
    position: absolute;
    left: 60px;
    top: 272px;
    list-style: none;
    color: var(--ink-soft);
    font-size: 17px;
  }
  .contact-list li {
    display: flex;
    align-items: center;
    gap: 16px;
    height: 30px;
  }
  .contact-list svg { width: 16px; height: 16px; fill: var(--ink-soft); flex: none; }
  .person {
    position: absolute;
    right: 60px;
    bottom: 70px;
    text-align: right;
    color: var(--ink);
  }
  .person__name { font-weight: 700; font-size: 26px; letter-spacing: 0.5px; }
  .person__role { font-size: 16px; color: var(--ink-soft); margin-top: 4px; }
  .brand--large {
    display: flex;
    align-items: center;
    gap: 26px;
    color: var(--mark-dark);
    font-weight: 800;
    font-size: 72px;
    text-transform: uppercase;
    letter-spacing: 1px;
  }
  .brand--large .brand__dot {
    width: 38px; height: 38px;
    background: var(--mark-dark);
  }
</style>
</head>
<body>
  <section class="card card--front">
    <div class="brand"><span class="brand__dot"></span>Resin Works Hub</div>

    <p class="address">7-4812 Fernhollow Road,<br>Abbotsford, BC, V3K 8R2</p>

    <ul class="contact-list">
      <li>
        <svg viewBox="0 0 16 16" aria-hidden="true"><path d="M3.6 1.2l2.3 2.6-1.3 1.7c.9 2 2.5 3.6 4.4 4.5l1.7-1.3 2.6 2.3-1.4 2.5C6.8 13.3 2.2 8.7 1.1 3.6z"/></svg>
        604-712-3390
      </li>
      <li>
        <svg viewBox="0 0 16 16" aria-hidden="true"><path d="M4.5 1h7a1 1 0 0 1 1 1v12a1 1 0 0 1-1 1h-7a1 1 0 0 1-1-1V2a1 1 0 0 1 1-1zm.5 2v9h6V3zm3 10a.8.8 0 1 0 0 1.6A.8.8 0 0 0 8 13z"/></svg>
        604-947-2164
      </li>
      <li>
        <svg viewBox="0 0 16 16" aria-hidden="true"><path d="M1 3.5h14v9H1zm1.4 1L8 8.8l5.6-4.3z"/></svg>
        ted@resinworkshub.ca
      </li>
      <li>
        <svg viewBox="0 0 16 16" aria-hidden="true"><path d="M8 1a7 7 0 1 0 0 14A7 7 0 0 0 8 1zm0 1.4c.8 0 1.8 1.7 2 4.1H6c.2-2.4 1.2-4.1 2-4.1zM2.5 8.8h2.2c.1 1.9.6 3.4 1.2 4.3a5.6 5.6 0 0 1-3.4-4.3zm0-1.6a5.6 5.6 0 0 1 3.4-4.3c-.6.9-1.1 2.4-1.2 4.3zm5.5 6.4c-.8 0-1.8-1.8-2-4.8h4c-.2 3-1.2 4.8-2 4.8zm2.1-.5c.6-.9 1.1-2.4 1.2-4.3h2.2a5.6 5.6 0 0 1-3.4 4.3zm1.2-5.9c-.1-1.9-.6-3.4-1.2-4.3a5.6 5.6 0 0 1 3.4 4.3z"/></svg>
        www.resinworkshub.ca
      </li>
    </ul>

    <div class="person">
      <p class="person__name">Ted Galloway</p>
      <p class="person__role">owner</p>
    </div>
  </section>

  <section class="card card--back">
    <div class="brand--large"><span class="brand__dot"></span>Resin Works Hub</div>
  </section>
</body>
</html>
```